Harborline Outpost Registry needs a web design

We are launching a new website and need a web design. The website is going to list every military base and installment around the world with information on each base such as a description of the base, the history of the base, contact information at the base, address, lat/long of the base, and any other relevant information including images of the base. We need a home page with navigation menu and the design of the military base page so that every military base page is formatted the same for the referenced information. We have included an example of the content that may be found on the base page(s). We are also going to have the information available in spanish.

We also wanted to mention we will be building this website in wordpress.

We also wanted to note that in the format of each base page, we will have a frequently asked questions section with answers.

```html
<!DOCTYPE html>
<html lang="en">
<head>
<meta charset="utf-8">
<title>Harborline Outpost Registry</title>
<link href="https://fonts.googleapis.com/css2?family=Poppins:wght@400;500;600;700&display=swap" rel="stylesheet">
<style>
:root{
  --yellow:#f7c513;
  --ink:#1a1a1a;
  --muted:#6b6b6b;
  --line:#e3e3e3;
  --page:#f2f2f2;
  --white:#ffffff;
  --black:#0d0d0d;
  --link:#2e5fa8;
}
*{box-sizing:border-box;margin:0;padding:0}
html,body{width:1200px;height:2772px;overflow:hidden}
body{font-family:"Poppins",sans-serif;color:var(--ink);background:var(--page);position:relative}
a{color:inherit;text-decoration:none}

.hero{position:absolute;left:0;top:0;width:1200px;height:620px;
  background:linear-gradient(180deg,#5b5a44 0%,#6f6b52 35%,#4a4a3c 70%,#2f2f28 100%);}
.hero-photo{position:absolute;inset:0;background:radial-gradient(ellipse at 70% 40%,rgba(170,160,120,.45),transparent 60%),radial-gradient(ellipse at 20% 80%,rgba(40,40,30,.6),transparent 60%)}
.hero-shade{position:absolute;inset:0;background:rgba(0,0,0,.25)}
.brand{position:absolute;left:100px;top:0;width:218px;height:72px;background:var(--yellow);
  display:flex;align-items:center;justify-content:center;text-align:center;font-weight:700;font-size:17px;line-height:1.2;color:var(--ink);padding:0 14px}
.nav{position:absolute;right:92px;top:18px;display:flex;align-items:center;gap:24px;color:var(--white);font-size:14px}
.nav .active{color:var(--yellow);border-bottom:2px solid var(--yellow);padding-bottom:2px}
.lang{display:flex;align-items:center;gap:4px;font-size:12px}
.btn{background:var(--yellow);color:var(--ink);font-weight:600;font-size:14px;padding:9px 14px;display:inline-block}
.hero-copy{position:absolute;left:0;right:0;top:256px;text-align:center;color:var(--white)}
.hero-copy .kicker{font-size:27px;font-weight:500}
.hero-copy h1{font-size:50px;font-weight:600;line-height:1.2}
.search{position:absolute;left:246px;top:372px;width:708px;height:50px;background:var(--white);display:flex}
.search span{flex:1;padding:0 16px;line-height:50px;font-size:14px;color:var(--muted)}
.search .go{width:56px;background:var(--yellow);display:flex;align-items:center;justify-content:center}
.dots{position:absolute;top:515px;left:0;right:0;display:flex;justify-content:center;gap:8px}
.dots i{width:8px;height:8px;border-radius:50%;background:rgba(255,255,255,.5)}
.dots i:first-child{background:var(--white)}

.section-bg{position:absolute;left:0;top:620px;width:1200px;height:1780px;
  background:linear-gradient(160deg,#e9e9e9 0%,#f7f7f7 40%,#eaeaea 100%)}
.section-title{position:absolute;left:80px;top:660px;font-size:34px;font-weight:600}

.listings{position:absolute;left:80px;top:740px;width:696px}
.card{height:194px;margin-bottom:18px;background:var(--white);box-shadow:0 2px 10px rgba(0,0,0,.14);padding:10px 14px;position:relative}
.filters{display:flex;gap:20px;font-size:10px;font-weight:500;padding-bottom:8px;border-bottom:1px solid var(--line)}
.row{display:flex;gap:18px;margin-top:14px}
.thumb{width:176px;height:122px;flex:none}
.info{flex:1;font-size:10px;color:var(--muted);line-height:1.55}
.info h3{font-size:14px;font-weight:600;color:var(--ink);margin-bottom:4px}
.info .links{display:flex;gap:26px;margin-top:8px;color:var(--link)}
.contact{width:170px;font-size:10px;text-align:right;line-height:1.6}
.contact b{font-weight:600}
.direction{position:absolute;right:18px;bottom:24px;font-size:10px;color:var(--link)}

.reviews{position:absolute;left:792px;top:740px;width:330px;height:1022px;background:var(--white);box-shadow:0 2px 10px rgba(0,0,0,.14);padding:22px 18px}
.reviews h2{font-size:18px;font-weight:600;padding-bottom:10px;border-bottom:1px solid var(--line);margin-bottom:18px}
.review{display:flex;flex-wrap:wrap;gap:12px;margin-bottom:32px}
.avatar{width:62px;height:62px;border-radius:50%;flex:none}
.who{font-size:14px;font-weight:600;line-height:1.4}
.stars{display:flex;gap:2px;margin:3px 0}
.who small{display:block;font-size:11px;font-weight:400;color:var(--muted)}
.review p{width:100%;font-size:11px;color:var(--muted);line-height:1.6}
.reviews .btn{position:absolute;left:120px;bottom:52px;padding:10px 20px}

.load{position:absolute;left:550px;top:2270px;padding:10px 22px}

.footer{position:absolute;left:0;top:2400px;width:1200px;height:372px;background:var(--black);color:var(--white);text-align:center}
.footer h2{font-size:32px;font-weight:600;margin-top:50px}
.footer-nav{display:flex;justify-content:center;gap:34px;font-size:14px;margin-top:24px}
.footer-nav span.sep{opacity:.6}
.footer-contact{position:absolute;left:130px;top:168px;width:940px;height:70px;border:1px solid #555;display:flex;align-items:center;justify-content:space-around;font-size:14px}
.footer-contact div{display:flex;align-items:center;gap:12px}
.ico{width:34px;height:34px;border-radius:50%;background:var(--yellow);display:flex;align-items:center;justify-content:center}
.copy{position:absolute;left:0;right:0;top:302px;font-size:12px}
</style>
</head>
<body>

<header class="hero">
  <div class="hero-photo" role="img" aria-label="Soldiers in the field with a drone overhead"></div>
  <div class="hero-shade"></div>
  <div class="brand">Harborline Outpost Registry</div>
  <nav class="nav">
    <a class="active">Home</a><a>About Us</a><a>Services</a><a>Our Military base</a>
    <span class="lang"><svg width="14" height="14" viewBox="0 0 14 14"><circle cx="7" cy="7" r="6" fill="none" stroke="#fff"/><path d="M1 7h12M7 1c3 3 3 9 0 12M7 1c-3 3-3 9 0 12" fill="none" stroke="#fff"/></svg>En</span>
    <a class="btn">Contact Us</a>
  </nav>
  <div class="hero-copy">
    <div class="kicker">Welcome To</div>
    <h1>Harborline Outpost Registry</h1>
  </div>
  <div class="search"><span>Search Location</span><div class="go"><svg width="20" height="20" viewBox="0 0 20 20"><circle cx="8" cy="8" r="6" fill="none" stroke="#1a1a1a" stroke-width="2"/><path d="M12.5 12.5l5 5" stroke="#1a1a1a" stroke-width="2"/></svg></div></div>
  <div class="dots"><i></i><i></i><i></i></div>
</header>

<div class="section-bg"></div>
<h2 class="section-title">Featured Listings</h2>

<main class="listings">
  <article class="card"><div class="filters"><span>Categories ▾</span><span>Locations ▾</span></div>
    <div class="row"><div class="thumb" role="img" aria-label="Ships docked at a naval base" style="background:linear-gradient(180deg,#bcd1e0,#8a6a55)"></div>
    <div class="info"><h3>Ridgeway Military Base</h3>Latitude 31.4820° N<br>Longitude 47.2915° W<br>Lorem ipsum dolor sit amet, consectetur adipiscing elit.<div class="links"><span>Email</span><span>Website</span></div></div>
    <div class="contact"><b>Number: (555) 014-2770</b><br>Address: Ridgeway, KY,<br>United States</div></div><span class="direction">Direction</span></article>

  <article class="card"><div class="filters"><span>Categories ▾</span><span>Locations ▾</span></div>
    <div class="row"><div class="thumb" role="img" aria-label="Base buildings at sunset" style="background:linear-gradient(180deg,#e6a45a,#6b4a34)"></div>
    <div class="info"><h3>Ridgeway Military Base</h3>Latitude 31.4820° N<br>Longitude 47.2915° W<br>Lorem ipsum dolor sit amet, consectetur adipiscing elit.<div class="links"><span>Email</span><span>Website</span></div></div>
    <div class="contact"><b>Number: (555) 014-2770</b><br>Address: Ridgeway, KY,<br>United States</div></div><span class="direction">Direction</span></article>

  <article class="card"><div class="filters"><span>Categories ▾</span><span>Locations ▾</span></div>
    <div class="row"><div class="thumb" role="img" aria-label="Base compound in hills" style="background:linear-gradient(180deg,#b8b3a3,#7a5f4c)"></div>
    <div class="info"><h3>Ridgeway Military Base</h3>Latitude 31.4820° N<br>Longitude 47.2915° W<br>Lorem ipsum dolor sit amet, consectetur adipiscing elit.<div class="links"><span>Email</span><span>Website</span></div></div>
    <div class="contact"><b>Number: (555) 014-2770</b><br>Address: Ridgeway, KY,<br>United States</div></div><span class="direction">Direction</span></article>

  <article class="card"><div class="filters"><span>Categories ▾</span><span>Locations ▾</span></div>
    <div class="row"><div class="thumb" role="img" aria-label="Aerial view of a base" style="background:linear-gradient(180deg,#8aa08a,#4d5a44)"></div>
    <div class="info"><h3>Ridgeway Military Base</h3>Latitude 31.4820° N<br>Longitude 47.2915° W<br>Lorem ipsum dolor sit amet, consectetur adipiscing elit.<div class="links"><span>Email</span><span>Website</span></div></div>
    <div class="contact"><b>Number: (555) 014-2770</b><br>Address: Ridgeway, KY,<br>United States</div></div><span class="direction">Direction</span></article>

  <article class="card"><div class="filters"><span>Categories ▾</span><span>Locations ▾</span></div>
    <div class="row"><div class="thumb" role="img" aria-label="Satellite view of a base" style="background:linear-gradient(135deg,#7d9a6a,#a9a98a)"></div>
    <div class="info"><h3>Ridgeway Military Base</h3>Latitude 31.4820° N<br>Longitude 47.2915° W<br>Lorem ipsum dolor sit amet, consectetur adipiscing elit.<div class="links"><span>Email</span><span>Website</span></div></div>
    <div class="contact"><b>Number: (555) 014-2770</b><br>Address: Ridgeway, KY,<br>United States</div></div><span class="direction">Direction</span></article>

  <article class="card"><div class="filters"><span>Categories ▾</span><span>Locations ▾</span></div>
    <div class="row"><div class="thumb" role="img" aria-label="Soldiers on patrol" style="background:linear-gradient(180deg,#6e6a55,#33322a)"></div>
    <div class="info"><h3>Ridgeway Military Base</h3>Latitude 31.4820° N<br>Longitude 47.2915° W<br>Lorem ipsum dolor sit amet, consectetur adipiscing elit.<div class="links"><span>Email</span><span>Website</span></div></div>
    <div class="contact"><b>Number: (555) 014-2770</b><br>Address: Ridgeway, KY,<br>United States</div></div><span class="direction">Direction</span></article>

  <article class="card"><div class="filters"><span>Categories ▾</span><span>Locations ▾</span></div>
    <div class="row"><div class="thumb" role="img" aria-label="Soldier at a coastal post" style="background:linear-gradient(180deg,#6f93b8,#5a4a3a)"></div>
    <div class="info"><h3>Ridgeway Military Base</h3>Latitude 31.4820° N<br>Longitude 47.2915° W<br>Lorem ipsum dolor sit amet, consectetur adipiscing elit.<div class="links"><span>Email</span><span>Website</span></div></div>
    <div class="contact"><b>Number: (555) 014-2770</b><br>Address: Ridgeway, KY,<br>United States</div></div><span class="direction">Direction</span></article>
</main>

<aside class="reviews">
  <h2>RECENT REVIEWS</h2>
  <div class="review"><div class="avatar" role="img" aria-label="Reviewer portrait" style="background:#8a7260"></div><div class="who">Arun Mehta<div class="stars"><svg width="76" height="13" viewBox="0 0 76 13"><g fill="#f7c513"><path id="s" d="M6.5 0l2 4.3 4.5.5-3.4 3 1 4.5-4.1-2.4-4 2.4 1-4.5L0 4.8l4.5-.5z"/><use href="#s" x="15.5"/><use href="#s" x="31"/><use href="#s" x="46.5"/></g><use href="#s" x="62" fill="#ccc"/></svg></div><small>03/05/2020 25:14</small></div>
    <p>Lorem ipsum dolor sit amet, consectetur adipiscing elit, sed do eiusmod tempor labore.</p></div>
  <div class="review"><div class="avatar" role="img" aria-label="Reviewer portrait" style="background:#c9b7a7"></div><div class="who">Priya Kapoor<div class="stars"><svg width="76" height="13" viewBox="0 0 76 13"><g fill="#f7c513"><use href="#s"/><use href="#s" x="15.5"/><use href="#s" x="31"/></g><g fill="#ccc"><use href="#s" x="46.5"/><use href="#s" x="62"/></g></svg></div><small>03/05/2020 25:14</small></div>
    <p>Lorem ipsum dolor sit amet, consectetur adipiscing elit, sed do eiusmod tempor labore.</p></div>
  <div class="review"><div class="avatar" role="img" aria-label="Reviewer portrait" style="background:#5d6b7c"></div><div class="who">Arun Mehta<div class="stars"><svg width="76" height="13" viewBox="0 0 76 13"><g fill="#f7c513"><use href="#s"/><use href="#s" x="15.5"/><use href="#s" x="31"/><use href="#s" x="46.5"/></g><use href="#s" x="62" fill="#ccc"/></svg></div><small>03/05/2020 25:14</small></div>
    <p>Lorem ipsum dolor sit amet, consectetur adipiscing elit, sed do eiusmod tempor labore.</p></div>
  <div class="review"><div class="avatar" role="img" aria-label="Reviewer portrait" style="background:#6b5046"></div><div class="who">Priya Kapoor<div class="stars"><svg width="76" height="13" viewBox="0 0 76 13"><g fill="#f7c513"><use href="#s"/><use href="#s" x="15.5"/><use href="#s" x="31"/></g><g fill="#ccc"><use href="#s" x="46.5"/><use href="#s" x="62"/></g></svg></div><small>03/05/2020 25:14</small></div>
    <p>Lorem ipsum dolor sit amet, consectetur adipiscing elit, sed do eiusmod tempor labore.</p></div>
  <a class="btn">View More</a>
</aside>

<a class="btn load">Load More</a>

<footer class="footer">
  <h2>Harborline Outpost Registry</h2>
  <nav class="footer-nav"><a>Home</a><span class="sep">|</span><a>About Us</a><span class="sep">|</span><a>Services</a><span class="sep">|</span><a>Our Military Base</a><span class="sep">|</span><a>Contact Us</a></nav>
  <div class="footer-contact">
    <div><span class="ico"><svg width="16" height="16" viewBox="0 0 16 16"><path d="M3 1l3 3-2 2c1 2 3 4 5 5l2-2 3 3-2 2C7 14 2 9 1 3z" fill="#1a1a1a"/></svg></span>(555) 014-2770</div>
    <div><span class="ico"><svg width="16" height="12" viewBox="0 0 16 12"><rect x="1" y="1" width="14" height="10" fill="none" stroke="#1a1a1a" stroke-width="1.6"/><path d="M1 1l7 6 7-6" fill="none" stroke="#1a1a1a" stroke-width="1.6"/></svg></span>info@harborlineregistry.example</div>
    <div><span class="ico"><svg width="12" height="16" viewBox="0 0 12 16"><path d="M6 0C3 0 0 2.4 0 6c0 4 6 10 6 10s6-6 6-10c0-3.6-3-6-6-6z" fill="#1a1a1a"/><circle cx="6" cy="6" r="2.2" fill="#f7c513"/></svg></span>Ridgeway, KY, United States</div>
  </div>
  <p class="copy">Copyright@2023 Harborline Outpost Registry All Rights Reserved</p>
</footer>

</body>
</html>
```